Modern corporate presentation

We need a clean, restrained company presentation in a modern Prezi style (design templates are attached for orientation). Please see the attachment for the briefing, colors and our corporate design.

content 1
Title:

FILOVAN
We connect worlds.
Digitization = increase in customer satisfaction

content 2
Animated on photo of company building (photo attached)

Text:

As Europe's leading service provider for business process outsourcing, we optimize your document management along the entire process chain of your document cycles, including physical long-term archiving after processing - efficiently, flexibly, individually and transparently!

content 3
Title: History
Overview of history as a timeline (see example design template slide 2) with dates and icons
Text:
1995
1997
2000
2016
2018
2021

content 4 or onwards
Morph transitions / individual seasons
1995 Founded by Lothar Brenner
1997 Start of ARKI@NET development
2000 real start ARKI@NET, certification GoB/S and KVR
2016 Development of Big Data + inMemory searches, first processes with AI
2018
ARKI@NET goes mobile
Expansion of the Siegen site with a new logistics center
Launch Papyrix concept
2021 More than 400 satisfied employees

content 5
Title: Facts and Figures
Animated to morph the following texts/numbers:

family business
400 employees at different locations
Own data centers
7,500 pallet spaces
50,000 active users daily on the ARKI@NET platform
525 000 receipts per month
210 customers from all over Europe
all necessary certifications

content 6
Title: Product and service portfolio
Combine yourself...
Create animation from Lego building blocks, which are put together, morph individually according to the order (1-3).

Module 1:
system platform
• Audit-proof archiving ARKI@NET
• Fully integrated document management
• Complete, certified KVR® integration

Module 2:
solution modules
• Digital files
• Invoice receipt workflow
ordering system
• Digital inbox
• Case management
• Data Lantern

Module 3:

process services
• Storage
• Scanning Service
• Collection Services
• BPO Inbox
• BPO invoice receipt

content 7
Title: Good Reasons / Benefits
Trust / full-service provider for document-based business processes completely own solution
Portfolio / depiction of the entire process chain from a single source
Experience / reference projects of all sizes and industries
Employees / All services are provided by our own staff without the involvement of subcontractors

content 8
Title: The 100% Philosophy

Overview of the following 3 main points, which are highlighted individually below:

The system
Services
Privacy and Certifications
___

The system
• 100% own data center with 24x7 operation, incl. backup data center
• Certified KVR partner
• Real, completely in-house developed SaaS solution for data center operations only
• Maintenance, support and updates included
• Web-based application

Services
• Combination of man & machine
• Service level agreements, service defined in terms of time
• Penalty for non-fulfilment

Privacy and certifications:
• All common certifications
• Own compliance management
• Data protection according to GDPR

Font styles to use
Other font styles liked:
• Myrlad Pro Bold für Head und Sublines, Lucida Grande Regular für Fließtexte

Requirements
Must have
• clean and reserved, taking our corporate design into account
Nice to have
• Prezi Style, seamless transitions (similar to a scrollipage)

```html
<!DOCTYPE html>
<html lang="de">
<head>
<meta charset="utf-8">
<title>Produkt und Leistungsportfolio</title>
<link rel="stylesheet" href="https://fonts.googleapis.com/css2?family=Source+Sans+3:wght@400;600;700&display=swap">
<style>
  :root{
    --ink:#2a333d;
    --text:#33383d;
    --rule:#c9c9c9;
    --panel:#f7f7f7;
    --bullet:#6b8599;
    --accent:#6b8599;
    --sand:#b7a98a;
    --ring:#e4e4e4;
    --ring-dark:#c5cad2;
    --footer:#2a333d;
    --white:#ffffff;
    --brick-top:#d4c8a8;
    --brick-grey:#9a9a9a;
    --brick-dark:#4a535c;
  }
  *{box-sizing:border-box;margin:0;padding:0}
  html,body{width:1200px;height:675px;overflow:hidden;background:var(--white)}
  body{font-family:"Source Sans 3",sans-serif;color:var(--text);position:relative}
  .slide{position:relative;width:1200px;height:675px}
  .slide-title{position:absolute;top:48px;left:0;width:1200px;text-align:center;font-weight:700;font-size:35px;color:var(--ink);letter-spacing:-0.3px}
  .title-rule{position:absolute;top:92px;left:116px;width:968px;height:1px;background:var(--rule)}
  .art{position:absolute;inset:0}
  .module-heading{position:absolute;font-weight:700;font-size:20px;color:var(--ink);letter-spacing:-0.2px}
  .panel{position:absolute;background:var(--panel)}
  .panel ul{list-style:none}
  .panel li{position:relative;padding-left:19px;font-size:14px;line-height:17px;margin-bottom:7px}
  .panel li::before{content:"";position:absolute;left:1px;top:5px;width:7px;height:7px;border-radius:50%;background:var(--bullet)}
  .panel-platform{left:180px;top:264px;width:219px;height:166px;padding:24px 10px 0 18px;clip-path:polygon(0 0,100% 0,100% 76%,80% 100%,0 100%)}
  .panel-services{left:781px;top:233px;width:228px;height:166px;padding:18px 10px 0 19px;clip-path:polygon(0 0,100% 0,100% 76%,80% 100%,0 100%)}
  .panel-modules{left:508px;top:458px;width:414px;height:108px;padding:20px 10px 0 21px;display:flex;gap:10px;clip-path:polygon(0 0,100% 0,100% 60%,89% 100%,0 100%)}
  .panel-modules ul{width:205px}
  .brick-area{position:absolute;left:502px;top:178px;width:166px;height:180px;border-radius:10px;
    background:linear-gradient(180deg,var(--brick-top) 0%,var(--brick-grey) 35%,var(--brick-dark) 55%,var(--brick-grey) 80%,#b5b5b5 100%)}
  .footer{position:absolute;left:0;top:608px;width:1200px;height:67px;background:var(--footer);color:var(--white)}
  .brand{position:absolute;left:119px;top:19px;display:flex;align-items:center;gap:6px;font-size:22px;font-weight:400;letter-spacing:0.5px;color:#e6e8ea}
  .brand-mark{width:16px;height:16px;background:#e6e8ea;border-radius:2px}
  .footer-label{position:absolute;right:164px;top:23px;font-size:15px;letter-spacing:1px}
  .footer-divider{position:absolute;left:1049px;top:16px;width:1px;height:51px;background:var(--white)}
  .page-number{position:absolute;left:1060px;top:18px;font-size:23px}
</style>
</head>
<body>
<main class="slide">
  <h1 class="slide-title">Produkt und Leistungsportfolio</h1>
  <div class="title-rule"></div>

  <svg class="art" width="1200" height="675" viewBox="0 0 1200 675" aria-hidden="true">
    <circle cx="581" cy="269" r="136" fill="none" stroke="#d8d8d8" stroke-width="1" stroke-dasharray="5 5"/>
    <path d="M448 278 A136 136 0 0 1 547 138" fill="none" stroke="var(--ring)" stroke-width="5"/>
    <path d="M672 168 A136 136 0 0 1 717 278" fill="none" stroke="var(--ring)" stroke-width="5"/>
    <path d="M472 348 A136 136 0 0 0 596 404" fill="none" stroke="var(--ring-dark)" stroke-width="5"/>
    <line x1="253" y1="205" x2="462" y2="205" stroke="#bdbdbd" stroke-width="1.5"/>
    <circle cx="462" cy="205" r="5" fill="#bdbdbd"/>
    <line x1="675" y1="172" x2="920" y2="172" stroke="#bdbdbd" stroke-width="1.5"/>
    <circle cx="675" cy="172" r="5" fill="#bdbdbd"/>
    <line x1="486" y1="339" x2="486" y2="406" stroke="var(--accent)" stroke-width="1.5"/>
    <circle cx="486" cy="339" r="5" fill="var(--accent)"/>
    <path d="M180 204 A37 37 0 0 1 253 204" fill="none" stroke="#bdbdbd" stroke-width="1.5"/>
    <circle cx="217" cy="207" r="29" fill="var(--panel)"/>
    <rect x="207" y="196" width="14" height="20" rx="2" fill="none" stroke="var(--sand)" stroke-width="1.5"/>
    <line x1="203" y1="219" x2="230" y2="219" stroke="var(--sand)" stroke-width="1.5"/>
    <path d="M920 172 A37 37 0 0 1 994 172" fill="none" stroke="#bdbdbd" stroke-width="1.5"/>
    <circle cx="957" cy="174" r="29" fill="var(--panel)"/>
    <circle cx="957" cy="168" r="8" fill="none" stroke="var(--sand)" stroke-width="1.5"/>
    <path d="M944 188 h26" stroke="var(--sand)" stroke-width="1.5"/>
    <path d="M467 404 A37 37 0 0 0 467 478" fill="none" stroke="var(--accent)" stroke-width="1.5"/>
    <circle cx="471" cy="441" r="29" fill="var(--panel)"/>
    <rect x="459" y="429" width="11" height="11" fill="none" stroke="var(--sand)" stroke-width="1.5"/>
    <rect x="472" y="429" width="11" height="11" fill="none" stroke="var(--sand)" stroke-width="1.5"/>
    <rect x="465" y="442" width="11" height="11" fill="none" stroke="var(--sand)" stroke-width="1.5"/>
  </svg>

  <div class="brick-area" role="img" aria-label="Illustration: dreischichtiger Baustein mit Noppen als Symbol für das kombinierbare Portfolio"></div>

  <h2 class="module-heading" style="left:180px;top:234px">Systemplattform</h2>
  <div class="panel panel-platform">
    <ul>
      <li>Revisionssichere Archivierung ARKI@NET</li>
      <li>Dokumentenmanagement voll integriert</li>
      <li>Vollständige, zertifizierte KVR® Integration</li>
    </ul>
  </div>

  <h2 class="module-heading" style="left:782px;top:198px">Prozessdienstleistungen</h2>
  <div class="panel panel-services">
    <ul>
      <li>Lagerung</li>
      <li>Scandienstleistung</li>
      <li>Erfassungsdienstleistungen</li>
      <li>BPO Posteingang</li>
      <li>BPO Rechnungseingang</li>
    </ul>
  </div>

  <h2 class="module-heading" style="left:508px;top:428px">Lösungsmodule</h2>
  <div class="panel panel-modules">
    <ul>
      <li>Digitale Akten</li>
      <li>Rechnungseingangsworkflow Bestellsystem</li>
    </ul>
    <ul>
      <li>Digitaler Posteingang</li>
      <li>Vorgangsmanagement</li>
      <li>Data Lantern</li>
    </ul>
  </div>

  <footer class="footer">
    <div class="brand"><span class="brand-mark"></span>FILOVAN</div>
    <div class="footer-label">PRESENTATION TITLE</div>
    <div class="footer-divider"></div>
    <div class="page-number">04</div>
  </footer>
</main>
</body>
</html>
```